Drone service provider needs a brilliant web design

I need a responsive web design for a new drone service company. Pelham Drone Solutions provides turnkey solutions to capture, process, and deliver actionable aerial data to customers. The design should communicate a professional company that is safe, legal and insured. I included our logo design and business card designs for reference.
*content to be supplied after design selected

Target Market(s)

We serve telecommunications, construction, government, utility infrastructure, insurance and other industries.

Industry/Entity Type

Industrial

Number of Pages Required

5+ page

Colors

Designer to choose colors to be used in the design.

Requirements
Must have
• The design should highlight professional services to include Inspections, Mapping, Consulting and Training. The site should include aerial images and video to compliment the services offered. The landing page must include following sections in order: HOME, SERVICES, ABOUT, DEMO REEL, CLIENTS, CONTACT FORM, and social media buttons (Facebook, LinkedIn, Twitter, YouTube, Instagram). Contact: 615-382-9041 info@pelhamdronesolutions-example.com Smyrna, TN
• Sitemap:
• 6 pages: Home, Inspections, Mapping, Training, Consulting, About
• HOME (Landing Page)
• • Header with logo and tab links (Home, Services, About, Contact)
• • 'CAPTURE. PROCESS. DELIVER.' tagline and 'CONTACT US' button displayed within aerial image of drone over city or construction site
• • Services section with icons, text and read more link to page
• • About section with photo and text with three icons for SAFE. LEGAL. INSURED.
• • Demo reel
• • Clients logos shown scrolling horizontally
• • Contact form
• • Footer with logo, phone, email, social media buttons
• SERVICES (4 different pages)
• • Inspections
• • Mapping
• • Consulting
• • Training
• ABOUT page
• • Company
• • Partners
• • Certifications & Associations
• • Careers
• CONTACT linked to bottom of landing page
• Would you like to receive the newsletter? Yes or No Drop-down list
Nice to have
• Photos of KVR Marlin or Corvex inspecting infrastructure, buildings, construction sites, etc. A photo of one or two pilots in vest and helmet. Free stock photos preferred but would purchase the right photo that's more relevant.
• website references:
• https://www.quillrotor-example.com/
• https://www.brentfieldworks-example.com/services
• https://www.tomaro-example.com/
• http://gantrymetric-example.com/
• http://lumbrook-example.com/
• http://fennotics-example.com/
• https://www.grebe-example.io/
Should not have
• not an aerial photography or videography service business, no blog or newsletter

```html
<!DOCTYPE html>
<html lang="en">
<head>
<meta charset="utf-8">
<title>Pelham Drone Solutions</title>
<link href="https://fonts.googleapis.com/css2?family=Michroma&family=Saira:wght@600;700&family=Jost:wght@400;500&display=swap" rel="stylesheet">
<style>
:root{
  --blue:#0073ae;
  --ink:#1f1f1f;
  --text:#3a3a3a;
  --bar:#2d2d2d;
  --footer:#323232;
  --soft:#f4f4f4;
  --white:#ffffff;
  --rule:#c9c9c9;
  --s1:#3b5998;--s2:#0077b5;--s3:#55acee;--s4:#e62117;--s5:#8a5a44;
}
*{box-sizing:border-box;margin:0;padding:0}
html,body{width:1200px;height:2643px;overflow:hidden}
body{position:relative;background:var(--white);font-family:"Jost",sans-serif;color:var(--text)}
.abs{position:absolute}
.heading{font-family:"Saira",sans-serif;font-weight:700;color:var(--ink)}

/* top bar */
.topbar{left:0;top:0;width:1200px;height:42px;background:var(--bar);color:var(--white);font-size:14px}
.topbar .contact{position:absolute;top:0;height:42px;display:flex;align-items:center;gap:8px}
.social{display:flex;gap:6px}
.social span{display:block;border-radius:50%}
.s1{background:var(--s1)}.s2{background:var(--s2)}.s3{background:var(--s3)}.s4{background:var(--s4)}.s5{background:var(--s5)}
.topbar .social{position:absolute;right:99px;top:8px}
.topbar .social span{width:26px;height:26px;border:1px solid rgba(255,255,255,.5)}

/* header */
.header{left:0;top:42px;width:1200px;height:108px;background:var(--white)}
.brand{font-family:"Saira",sans-serif;font-weight:700;color:var(--ink);line-height:1}
.header .brand{position:absolute;left:100px;top:22px}
.brand .name{font-size:44px;letter-spacing:2px}
.brand .sub{font-size:15px;letter-spacing:5px;margin-top:2px}
.nav{position:absolute;left:0;top:41px;width:1200px;font-family:"Saira",sans-serif;font-weight:700;font-size:18px;color:var(--ink)}
.nav a{position:absolute;white-space:nowrap;text-decoration:none;color:inherit}
.nav .active{color:var(--blue)}
.nav .active::after{content:"";position:absolute;left:0;right:0;bottom:-8px;height:3px;background:var(--blue)}

/* hero */
.hero{left:0;top:150px;width:1200px;height:495px;background:linear-gradient(160deg,#e6e8ea 0%,#c8ccd0 45%,#8c9096 75%,#6b6f60 100%)}
.hero-caption{left:0;top:596px;width:1200px;height:49px;background:rgba(40,40,40,.55);color:var(--white);font-family:"Michroma",sans-serif;font-size:26px;text-align:center;line-height:49px;letter-spacing:1px}

/* section titles */
.title{width:1200px;left:0;text-align:center;font-size:32px;line-height:40px}
.title .accent{color:var(--blue)}
.title .small{font-size:22px}
.divider{left:465px;width:270px;height:1px;background:var(--rule)}
.divider::after{content:"";position:absolute;left:100px;top:-1px;width:70px;height:3px;background:var(--blue)}

.btn{display:flex;align-items:center;justify-content:space-between;background:var(--blue);color:var(--white);border-radius:20px;font-size:14px;padding:0 4px 0 14px;text-transform:uppercase}
.btn i{display:block;width:24px;height:24px;border-radius:50%;background:var(--white);position:relative}
.btn i::after{content:"";position:absolute;left:7px;top:8px;width:6px;height:6px;border-top:2px solid var(--blue);border-right:2px solid var(--blue);transform:rotate(45deg)}

/* about */
.about-text{left:102px;top:793px;width:994px;text-align:center;font-size:14px;line-height:22px}

/* services */
.services{left:0;top:1024px;width:1200px;height:541px;background:var(--soft)}
.service{width:240px;text-align:center}
.service .ring{width:127px;height:127px;margin:0 auto;border-radius:50%;border:5px solid #e6e6e6;background:var(--white);display:flex;align-items:center;justify-content:center}
.service h3{font-family:"Saira",sans-serif;font-weight:700;color:var(--ink);font-size:21px;line-height:26px;margin-top:22px}
.service p{font-size:13.5px;line-height:23px;margin-top:10px}
.service .btn{width:113px;height:30px;margin:12px auto 0;font-size:11px;padding-left:12px}
.service .btn i{width:22px;height:22px}
.service .btn i::after{left:6px;top:7px}

/* map area */
.map{left:0;top:1565px;width:1200px;height:562px;background:linear-gradient(135deg,#e9e6dc 0%,#efeee6 50%,#dfe6d6 100%)}
.map-photo{left:396px;top:1640px;width:406px;height:140px;border:4px solid #bdbdbd;background:linear-gradient(180deg,#9fb8d6 0%,#6f8fb4 55%,#3a5677 100%)}

/* footer */
.footer{left:0;top:2127px;width:1200px;height:516px;background:var(--footer)}
.card{left:99px;top:1864px;width:502px;height:439px;background:var(--white);text-align:center}
.card .brand{margin-top:80px}
.card .brand .name{font-size:40px}
.card .brand .sub{font-size:14px;letter-spacing:5px}
.card h4{font-family:"Saira",sans-serif;font-weight:700;color:var(--ink);font-size:21px;margin-top:24px}
.card .social{justify-content:center;margin-top:6px;gap:5px}
.card .social span{width:25px;height:25px}
.card p{font-size:14px;line-height:24px;margin:30px auto 0;width:370px}

.inquiry{left:601px;top:1864px;width:500px;height:439px;background:var(--blue);color:var(--white);padding:30px 40px 0}
.inquiry h2{font-family:"Saira",sans-serif;font-weight:700;font-size:26px;line-height:32px}
.inquiry .bar{width:150px;height:1px;background:rgba(255,255,255,.5);margin-top:12px;position:relative}
.inquiry .bar::after{content:"";position:absolute;left:0;top:-1px;width:70px;height:3px;background:var(--white)}
.field{border-bottom:1px solid rgba(255,255,255,.7);font-size:14px;padding-bottom:10px;margin-top:22px;width:418px}
.field.message{height:60px}
.submit{width:118px;height:38px;margin-top:34px;background:var(--bar);border-radius:20px;display:flex;align-items:center;justify-content:space-between;padding:0 5px 0 22px;font-size:15px}
.submit i{display:block;width:26px;height:26px;border-radius:50%;background:var(--white);position:relative}
.submit i::after{content:"";position:absolute;left:8px;top:9px;width:6px;height:6px;border-top:2px solid var(--bar);border-right:2px solid var(--bar);transform:rotate(45deg)}

.footnav{left:0;top:2350px;width:1200px;font-family:"Saira",sans-serif;font-weight:700;color:var(--white);font-size:18px}
.footnav span{position:absolute;white-space:nowrap}
.finfo{width:300px;text-align:center;color:var(--white);font-size:15px}
.finfo .icon{width:56px;height:56px;border-radius:50%;background:var(--blue);border:3px solid var(--white);margin:0 auto 20px;display:flex;align-items:center;justify-content:center}
.footrule{left:99px;top:2583px;width:1002px;height:1px;background:#5a5a5a}
.copyright{left:0;top:2600px;width:1200px;text-align:center;color:var(--white);font-size:14px}
</style>
</head>
<body>

<div class="abs topbar">
  <div class="contact" style="left:100px">
    <svg width="16" height="16" viewBox="0 0 24 24"><path fill="#fff" d="M6.6 10.8a15.1 15.1 0 0 0 6.6 6.6l2.2-2.2c.3-.3.7-.4 1-.2 1.1.4 2.3.6 3.6.6.6 0 1 .4 1 1V20c0 .6-.4 1-1 1A17 17 0 0 1 3 4c0-.6.4-1 1-1h3.5c.6 0 1 .4 1 1 0 1.3.2 2.5.6 3.6.1.3 0 .7-.2 1z"/></svg>
    <span>615-382-9041</span>
  </div>
  <div class="contact" style="left:250px">
    <svg width="17" height="13" viewBox="0 0 24 18"><rect width="24" height="18" rx="2" fill="#fff"/><path d="M1 2l11 8 11-8" fill="none" stroke="#2d2d2d" stroke-width="2"/></svg>
    <span>info@pelhamdronesolutions-example.com</span>
  </div>
  <div class="social" aria-label="Social media links">
    <span class="s1"></span><span class="s2"></span><span class="s3"></span><span class="s4"></span><span class="s5"></span>
  </div>
</div>

<header class="abs header">
  <div class="brand"><div class="name">PELHAM</div><div class="sub">DRONE SOLUTIONS</div></div>
  <nav class="nav">
    <a class="active" style="left:555px">HOME</a>
    <a style="left:671px">ABOUT US</a>
    <a style="left:828px">SERVICES</a>
    <a style="left:981px">CONTACT US</a>
  </nav>
</header>

<div class="abs hero" role="img" aria-label="Drone hovering beside a pilot in a hard hat and hi-vis vest at a high-rise construction site"></div>
<div class="abs hero-caption">Capture • Process • Deliver</div>

<h2 class="abs heading title" style="top:714px">ABOUT PELHAM <span class="accent small">DRONE SOLUTIONS</span></h2>
<div class="abs divider" style="top:772px"></div>
<p class="abs about-text">Lorem ipsum dolor sit amet, consectetur adipiscing elit, sed do eiusmod tempor incididunt ut labore et dolore magna aliqua. Ut enim ad minim veniam, quis nostrud exercitation ullamco laboris nisi ut aliquip ex ea commodo consequat. Duis aute irure dolor in reprehenderit in voluptate velit esse cillum dolore eu fugiat nulla pariatur. Excepteur sint occaecat cupidatat non proident, sunt in culpa qui officia deserunt mollit anim id est laborum. Lorem ipsum dolor sit amet, consectetur adipiscing elit, sed do eiusmod tempor incididunt ut labore et dolore magna aliqua.</p>
<div class="abs btn" style="left:532px;top:910px;width:136px;height:38px">Read More<i></i></div>

<section class="abs services"></section>
<h2 class="abs heading title" style="top:1094px">OUR <span class="accent">SERVICES</span></h2>
<div class="abs divider" style="top:1152px"></div>

<div class="abs service" style="left:90px;top:1190px">
  <div class="ring"><svg width="50" height="58" viewBox="0 0 50 58"><rect x="4" y="6" width="42" height="50" rx="4" fill="none" stroke="var(--blue)" stroke-width="4"/><rect x="16" y="1" width="18" height="10" rx="2" fill="var(--blue)"/><g fill="var(--blue)"><rect x="11" y="20" width="6" height="6"/><rect x="11" y="32" width="6" height="6"/><rect x="11" y="44" width="6" height="6"/><rect x="21" y="22" width="18" height="3"/><rect x="21" y="34" width="18" height="3"/><rect x="21" y="46" width="18" height="3"/></g></svg></div>
  <h3>INSPECTIONS</h3>
  <p>Lorem ipsum dolr amet, consectetur adipiscing elit, sed do eiusmod tem incididunt ut labore et.</p>
  <div class="btn">Read More<i></i></div>
</div>
<div class="abs service" style="left:349px;top:1190px">
  <div class="ring"><svg width="60" height="56" viewBox="0 0 60 56"><rect x="22" y="6" width="34" height="28" fill="none" stroke="var(--blue)" stroke-width="4"/><circle cx="10" cy="10" r="6" fill="var(--blue)"/><path d="M3 20h14l12 4v4l-12-1v26H3z" fill="var(--blue)"/><path d="M39 34l-8 18M39 34l8 18" stroke="var(--blue)" stroke-width="3"/></svg></div>
  <h3>TRAINING</h3>
  <p>Lorem ipsum dolr amet, consectetur adipiscing elit, sed do eiusmod tem incididunt ut labore et.</p>
  <div class="btn">Read More<i></i></div>
</div>
<div class="abs service" style="left:610px;top:1190px">
  <div class="ring"><svg width="60" height="56" viewBox="0 0 60 56"><path d="M2 26l16-5 16 5 18-6v32l-18 6-16-5-16 5z" fill="var(--blue)"/><path d="M34 2a10 10 0 0 1 10 10c0 8-10 18-10 18S24 20 24 12A10 10 0 0 1 34 2z" fill="var(--blue)" stroke="#fff" stroke-width="2"/><circle cx="34" cy="12" r="4" fill="#fff"/></svg></div>
  <h3>MAPPING</h3>
  <p>Lorem ipsum dolr amet, consectetur adipiscing elit, sed do eiusmod tem incididunt ut labore et.</p>
  <div class="btn">Read More<i></i></div>
</div>
<div class="abs service" style="left:870px;top:1190px">
  <div class="ring"><svg width="68" height="40" viewBox="0 0 68 40"><path d="M0 6l14-4 8 22-12 4zM68 6L54 2l-8 22 12 4z" fill="var(--blue)"/><path d="M16 8l12-2 8 4 10-4 8 2 4 16-16 12c-2 2-5 2-7 0L18 26z" fill="var(--blue)"/></svg></div>
  <h3>CONSULTING</h3>
  <p>Lorem ipsum dolr amet, consectetur adipiscing elit, sed do eiusmod tem incididunt ut labore et.</p>
  <div class="btn">Read More<i></i></div>
</div>

<div class="abs map" role="img" aria-label="Road map of the central United States with a location marker"></div>
<div class="abs map-photo" role="img" aria-label="Photo of a waterfront city skyline at dusk"></div>

<footer class="abs footer"></footer>

<div class="abs card">
  <div class="brand"><div class="name">PELHAM</div><div class="sub">DRONE SOLUTIONS</div></div>
  <h4>FOLLOW US ON</h4>
  <div class="social" aria-label="Social media links">
    <span class="s1"></span><span class="s2"></span><span class="s3"></span><span class="s4"></span><span class="s5"></span>
  </div>
  <p>Lorem ipsum dolor sit amet, consectetuer adipiscing elit, sed diam nonummy nibh euismod tincidunt ut laoreet dolore magna aliquam erat volutpat. Ut wisi enim ad minim veniam.</p>
</div>

<div class="abs inquiry">
  <h2>QUICK INQUIRY</h2>
  <div class="bar"></div>
  <div class="field" style="margin-top:24px">Name</div>
  <div class="field">Email</div>
  <div class="field">Subject</div>
  <div class="field message">Message</div>
  <div class="submit">SUBMIT<i></i></div>
</div>

<nav class="abs footnav">
  <span style="left:326px">HOME</span>
  <span style="left:444px">ABOUT US</span>
  <span style="left:601px">SERVICES</span>
  <span style="left:755px">CONTACT US</span>
</nav>

<div class="abs finfo" style="left:135px;top:2434px">
  <div class="icon"><svg width="20" height="26" viewBox="0 0 20 26"><path d="M10 0a10 10 0 0 1 10 10c0 7-10 16-10 16S0 17 0 10A10 10 0 0 1 10 0z" fill="#fff"/><circle cx="10" cy="10" r="4" fill="var(--blue)"/></svg></div>
  123, Lorem ipsum dolor sit amet
</div>
<div class="abs finfo" style="left:456px;top:2434px">
  <div class="icon"><svg width="24" height="24" viewBox="0 0 24 24"><path fill="#fff" d="M6.6 10.8a15.1 15.1 0 0 0 6.6 6.6l2.2-2.2c.3-.3.7-.4 1-.2 1.1.4 2.3.6 3.6.6.6 0 1 .4 1 1V20c0 .6-.4 1-1 1A17 17 0 0 1 3 4c0-.6.4-1 1-1h3.5c.6 0 1 .4 1 1 0 1.3.2 2.5.6 3.6.1.3 0 .7-.2 1z"/></svg></div>
  615-382-9041
</div>
<div class="abs finfo" style="left:773px;top:2434px">
  <div class="icon"><svg width="26" height="22" viewBox="0 0 26 22"><rect x="1" y="4" width="24" height="17" rx="2" fill="none" stroke="#fff" stroke-width="2"/><path d="M1 6l12 8 12-8" fill="none" stroke="#fff" stroke-width="2"/></svg></div>
  info@pelhamdronesolutions-example.com
</div>

<div class="abs footrule"></div>
<div class="abs copyright">Copyright © 2018 PELHAM DRONE SOLUTIONS. All Rights Reserved.</div>

</body>
</html>
```